New Bicycle shop business card

Hi!
I'm looking for a business card for my new proffesional bike mechanics shop. This shop is only for fixing broken bikes and not selling bikes.
Peferbly a modern and sleek and modern design.
Colors: black, grey, red, white
Information:
Name: Rijwielwerkplaats Vanhoutte
Shop owner: Bart Vanhoutte & Marieke Segers
Website: www.rijwielwerkplaats-vanhoutte.be
Email: info@rijwielwerkplaats-vanhoutte.be
Phone number: +32471902368
Street adres: Kerkweg 46
9940 Bellebeke
Slogan/shop information: Herstellingen van alle merken.
Logo: see files.
Target Market(s)
People who seek a mechanic to fix or upgrade their bikes.
Contact Information for Business Card
Information:
Website: info@rijwielwerkplaats-vanhoutte.be
9940 Bellebeke
Logo: see files.

```html
<!DOCTYPE html>
<html lang="nl">
<head>
<meta charset="utf-8">
<title>Rijwielwerkplaats Vanhoutte – Visitekaartje</title>
<link rel="stylesheet" href="https://fonts.googleapis.com/css2?family=Lato:wght@400;700;900&display=swap">
<style>
  :root {
    --bg: #2a2a2c;
    --card: #1d1e20;
    --card-back: #1a1b1d;
    --pattern: #232427;
    --red: #e3173e;
    --white: #f4f4f4;
    --grey: #b9b9bb;
    --rule: #6c6c70;
  }
  * { box-sizing: border-box; margin: 0; padding: 0; }
  html, body { width: 1200px; height: 1108px; overflow: hidden; }
  body {
    background: var(--bg);
    font-family: "Lato", sans-serif;
    display: flex;
    align-items: center;
    justify-content: center;
    gap: 80px;
  }
  .card {
    width: 420px;
    height: 680px;
    border-radius: 22px;
    position: relative;
    box-shadow: 0 18px 40px rgba(0,0,0,.45);
  }
  .card--front {
    background: var(--card);
    display: flex;
    flex-direction: column;
    align-items: center;
    text-align: center;
    padding: 130px 40px 0;
  }
  .brand-mark {
    width: 46px; height: 46px;
    background: var(--red);
    border-radius: 50%;
    margin-bottom: 26px;
  }
  .brand-name {
    font-weight: 900;
    color: var(--white);
    font-size: 27px;
    line-height: 1.15;
    letter-spacing: 1.5px;
    text-transform: uppercase;
  }
  .owners {
    margin-top: 44px;
    color: var(--red);
    font-size: 19px;
    font-weight: 400;
    text-transform: uppercase;
    letter-spacing: .2px;
  }
  .role { color: var(--grey); font-size: 18px; margin-top: 2px; }
  .icon-rule {
    display: flex; align-items: center; gap: 6px;
    width: 200px; margin: 18px 0 10px;
  }
  .icon-rule::before, .icon-rule::after {
    content: ""; flex: 1; height: 1px; background: var(--rule);
  }
  .icon-rule svg { width: 24px; height: 24px; display: block; }
  .contact { color: var(--white); font-size: 18px; line-height: 1.45; }
  .divider { width: 200px; height: 1px; background: var(--rule); margin: 10px 0 14px; }
  .address { color: var(--white); font-size: 19px; line-height: 1.4; }

  .card--back {
    background: var(--card-back);
    overflow: hidden;
  }
  .pattern-field {
    position: absolute; inset: 0 0 160px 0;
    background: linear-gradient(180deg, var(--pattern) 0%, var(--card-back) 100%);
  }
  .back-brand {
    position: absolute; left: 0; right: 0; top: 500px;
    display: flex; flex-direction: column; align-items: center; gap: 10px;
  }
  .back-brand .brand-mark { width: 34px; height: 34px; margin: 0; }
  .back-brand .brand-name { font-size: 14px; letter-spacing: 1px; }
  .tagline {
    position: absolute; left: 0; right: 0; top: 590px;
    text-align: center;
    color: var(--white);
    font-size: 20px;
    text-transform: uppercase;
    letter-spacing: .3px;
  }
</style>
</head>
<body>
  <section class="card card--front">
    <div class="brand-mark"></div>
    <h1 class="brand-name">Rijwielwerkplaats<br>Vanhoutte</h1>
    <p class="owners">Bart Vanhoutte &amp; Marieke Segers</p>
    <p class="role">Owner</p>
    <div class="icon-rule">
      <svg viewBox="0 0 24 24" aria-label="telefoon"><circle cx="12" cy="12" r="12" fill="#e3173e"/><path d="M8 6.5l2 .3.8 2.7-1.3 1c.7 1.5 1.8 2.6 3.3 3.3l1-1.3 2.7.8.3 2c-.3.8-1 1.2-1.8 1.1C10.6 16 8 13.4 6.9 8.3 6.8 7.5 7.2 6.8 8 6.5z" fill="#1d1e20"/></svg>
      <svg viewBox="0 0 24 24" aria-label="e-mail"><circle cx="12" cy="12" r="12" fill="#e3173e"/><rect x="6" y="8" width="12" height="8.5" rx="1" fill="#1d1e20"/><path d="M6.5 8.6L12 13l5.5-4.4" stroke="#e3173e" stroke-width="1.2" fill="none"/></svg>
      <svg viewBox="0 0 24 24" aria-label="website"><circle cx="12" cy="12" r="12" fill="#e3173e"/><circle cx="12" cy="12" r="6" fill="none" stroke="#1d1e20" stroke-width="1.6"/><ellipse cx="12" cy="12" rx="2.6" ry="6" fill="none" stroke="#1d1e20" stroke-width="1.2"/><path d="M6 12h12" stroke="#1d1e20" stroke-width="1.2"/></svg>
    </div>
    <p class="contact">+32471902368<br>info@rijwielwerkplaats-vanhoutte.be<br>www.rijwielwerkplaats-vanhoutte.be</p>
    <div class="divider"></div>
    <p class="address">Kerkweg 46<br>9940 Bellebeke</p>
  </section>

  <section class="card card--back">
    <div class="pattern-field" role="img" aria-label="Faint repeated brand mark pattern in dark grey"></div>
    <div class="back-brand">
      <div class="brand-mark"></div>
      <span class="brand-name">Rijwielwerkplaats Vanhoutte</span>
    </div>
    <p class="tagline">Herstellingen van alle merken</p>
  </section>
</body>
</html>
```